Employment Agency Website Design

We are working with an employment agency in California.

Some sites to use for content/competitors and inspiration:

https://www.pinecrestjobs.com/us/en
https://www.velmorusa.com
https://www.dravenworks.us
https://www.quillora.com/en
https://www.tomvalusa.com
https://www.fernstaffing.com

Thank you for taking the time to consider designing a website for us. We are web developers based in Stockton, CA, USA. Most of our projects go through the same process. Understanding this process may help you win a project with us. We custom-code all of our websites in-house. We don’t have any requirements as to what tools you use for your design, but we prefer Figma files. For any design that we label as four-stars, we send it to the client for review. The client picks the final design they want us to use. Once we complete this process, we will continue to show additional clients all the four-star sites and purchase them later. Your designs will have multiple chances to sell. For better chances of success, we ask that you follow these guidelines.

IMAGES:
If you use any images or icons in the design, we ask that you have a link to the asset so we can purchase the image/icon. Most of the designs we submit do not have the customer’s images on them unless they have some great images. Be creative; show us the feeling you are trying to portray with your image choices. Use any royalty-free site you choose. We subscribe to Adobe and mainly use their images, but we can purchase images outside of Adobe. PLEASE NOTE: we will not submit designs to clients with watermarks on the images.

FONTS:
We ask that you identify the fonts used in the design. This can be done in a message if you want. We typically use Google Fonts and Adobe Fonts.

CONTENT:
We're always open to different content and ideas. We often submit designs with stock images so the client can see our vision. We typically take pictures after the website launch to use their images with our vision. Lorem Ipsum is fine for paragraphs, but we ask that you write the headers in correct English. We want to be able to show the vision and identify the sections of the website.

INSPIRATION:
We typically add a couple of links in the brief of websites we like to help you get started in your design.

REVISIONS:
We do not often ask for revisions of the designs unless we see something in the design that may not appeal to the client. If there are slight changes that we want to make, we do that in the development process.

FEEDBACK:
We rarely give feedback on designs during the design process. We are working on many website projects and do not have the time to provide feedback. We usually respond if your request is well thought out and asks specific questions, but a note asking “feedback, please” usually goes unanswered.

```html
<!DOCTYPE html>
<html lang="en">
<head>
<meta charset="utf-8">
<title>Kestrel Talent — Employment Agency</title>
<link href="https://fonts.googleapis.com/css2?family=Work+Sans:wght@400;500;600;700;800&display=swap" rel="stylesheet">
<style>
:root{
  --brand:#C41E2F;
  --brand-bright:#FF2B3F;
  --brand-deep:#B81A2B;
  --ink:#1F1F1F;
  --muted:#555;
  --soft:#777;
  --page:#F8F8F8;
  --white:#fff;
  --rule:#C9C9C9;
}
*{box-sizing:border-box;margin:0;padding:0}
html,body{width:1200px;height:3064px;overflow:hidden}
body{background:var(--page);font-family:"Work Sans",sans-serif;color:var(--ink);position:relative}
.abs{position:absolute}
a{color:inherit;text-decoration:none}

/* header */
.brand{display:flex;align-items:center;gap:6px;font-weight:600;color:var(--brand)}
.brand-mark{width:18px;height:18px;background:var(--brand);border-radius:50%}
.site-brand{left:124px;top:24px;font-size:18px}
.main-nav{left:365px;top:28px;display:flex;gap:26px;font-size:11px;color:var(--ink)}
.main-nav .active{color:var(--brand)}
.caret{font-size:8px;margin-left:3px}
.search-icon{left:896px;top:26px}
.btn{display:flex;align-items:center;justify-content:center;border-radius:4px;font-size:16px;font-weight:500}
.btn-solid{background:var(--brand);color:var(--white);box-shadow:0 3px 6px rgba(0,0,0,.18)}
.btn-outline{border:1px solid var(--brand);color:var(--brand)}
.btn-light{background:var(--white);color:var(--brand);box-shadow:0 3px 6px rgba(0,0,0,.12)}
.btn-ghost{border:1px solid var(--white);color:var(--white)}
.sign-in{left:937px;top:13px;width:143px;height:46px}

/* hero */
.hero-title{left:120px;top:214px;font-size:31px;font-weight:500;line-height:37px}
.hero-title strong{color:var(--brand);font-weight:700}
.hero-lead{left:120px;top:304px;width:388px;font-size:16px;line-height:20px;color:var(--muted);text-align:justify;letter-spacing:.2px}
.btn-quote{left:120px;top:429px;width:225px;height:47px}
.btn-join{left:365px;top:429px;width:143px;height:47px}
.hero-art{left:583px;top:172px;width:500px;height:425px}

/* bands */
.band{left:0;width:1200px;background:var(--brand)}
.eyebrow{font-size:16px;letter-spacing:7px;text-transform:uppercase}
.section-title{font-size:31px;font-weight:700}
.on-red{color:var(--white)}
.center{left:0;width:1200px;text-align:center}

/* about */
.about-band{top:705px;height:541px}
.about-blob{left:118px;top:722px}
.about-photo{left:182px;top:765px;width:326px;height:379px;border-radius:12px;background:linear-gradient(135deg,#8f9aa3,#5d6168 55%,#3a3836);box-shadow:0 6px 14px rgba(0,0,0,.25)}
.about-eyebrow{left:610px;top:796px}
.about-title{left:610px;top:823px;width:420px;font-size:30px;line-height:37px}
.about-text{left:610px;top:924px;width:470px;font-size:16px;line-height:23.3px;text-align:justify;letter-spacing:.3px}
.btn-team{left:610px;top:1068px;width:225px;height:46px}

/* why */
.why-eyebrow{top:1305px;color:var(--brand)}
.why-title{top:1332px;color:#3a3a3a}
.why-lead{left:150px;width:900px;top:1390px;text-align:center;font-size:17px;line-height:23px;color:var(--soft)}
.stat{top:1478px;width:290px;text-align:center}
.stat-label{font-size:16px}
.stat-value{font-size:31px;font-weight:700;color:var(--brand);margin-top:22px}
.stat-note{font-size:11px;line-height:16.5px;color:var(--soft);margin-top:20px}
.stat-rule{top:1478px;width:1px;height:130px;background:var(--rule)}

/* procedure */
.proc-band{top:1665px;height:416px}
.proc-eyebrow{top:1715px}
.proc-title{top:1742px}
.proc-text{left:120px;top:1810px;width:490px;font-size:16px;line-height:23.2px;text-align:justify;letter-spacing:.3px}
.proc-duration-label{left:120px;top:1950px;font-size:16px}
.proc-duration{left:120px;top:1993px;font-size:31px;font-weight:700}
.proc-steps{left:697px;top:1808px;list-style:none;font-size:15px;font-weight:700;line-height:26.8px;z-index:2}
.proc-steps li{white-space:nowrap}
.proc-steps li::before{content:"•";margin-left:-16px;margin-right:8px;font-size:12px}
.btn-consult{left:672px;top:1987px;width:225px;height:45px;font-size:16px}
.proc-art{left:955px;top:1780px;width:118px;height:256px;border-radius:40px;background:linear-gradient(180deg,#e9e6e6,#bcb3b3);opacity:.9}

/* insights */
.ins-eyebrow{top:2122px;color:var(--brand)}
.ins-title{top:2150px;color:#333}
.card{top:2213px;width:306px}
.card-img{height:183px}
.card-title{margin-top:14px;font-size:17px;font-weight:500;color:var(--brand)}
.card-text{margin-top:6px;font-size:11px;line-height:16px;color:var(--soft);text-align:justify}
.card-link{display:inline-block;margin-top:7px;font-size:9px;color:var(--brand);text-decoration:underline}
.btn-more{left:937px;top:2517px;width:143px;height:39px;font-size:16px;border-radius:4px}

/* cta */
.cta-band{top:2604px;height:208px;background:linear-gradient(100deg,#c41e2f 0%,#c9293a 55%,#cf3444 100%)}
.cta-title{left:120px;top:2660px;font-size:30px}
.cta-text{left:120px;top:2716px;width:560px;font-size:16px;line-height:20px;letter-spacing:.3px}
.btn-contact{left:855px;top:2685px;width:225px;height:46px}

/* footer */
.footer-brand{left:124px;top:2862px;font-size:28px;font-weight:500}
.footer-brand .brand-mark{width:28px;height:28px}
.footer-contact{left:120px;top:2920px;font-size:16px;line-height:30px}
.footer-col{top:2852px;font-size:16px;line-height:33px}
.footer-col h4{color:var(--brand);font-weight:700;font-size:16px}
.footer-rule{left:120px;top:2999px;width:960px;height:1px;background:var(--brand)}
.copyright{left:120px;top:3016px;font-size:11px}
.social{top:3011px;display:flex;gap:13px;left:981px}
.social span{width:24px;height:24px;border-radius:50%;background:#f1d6d9;display:block;position:relative}
.social span::after{content:"";position:absolute;left:8px;top:8px;width:8px;height:8px;border-radius:50%;background:var(--brand)}
</style>
</head>
<body>

<header>
  <a class="abs brand site-brand" href="#"><span class="brand-mark"></span>Kestrel Talent</a>
  <nav class="abs main-nav">
    <a class="active" href="#">Home</a>
    <a href="#">Find Jobs<span class="caret">▾</span></a>
    <a href="#">Hire Talent<span class="caret">▾</span></a>
    <a href="#">About Us</a>
    <a href="#">Insight<span class="caret">▾</span></a>
  </nav>
  <svg class="abs search-icon" width="20" height="20" viewBox="0 0 20 20" aria-label="Search"><circle cx="8.5" cy="8.5" r="7" fill="none" stroke="#C41E2F" stroke-width="1.8"/><line x1="13.5" y1="13.5" x2="19" y2="19" stroke="#C41E2F" stroke-width="1.8"/></svg>
  <a class="abs btn btn-solid sign-in" href="#">Sign in</a>
</header>

<section class="hero">
  <h1 class="abs hero-title">Discover Your Potential<br>with <strong>Kestrel Talent!</strong></h1>
  <p class="abs hero-lead">Embark on a Journey of Professional Growth and Success with Kestrel Talent, Where Your Ambitions Meet Infinite Possibilities</p>
  <a class="abs btn btn-solid btn-quote" href="#">Request Quotation</a>
  <a class="abs btn btn-outline btn-join" href="#">Join as Talent</a>
  <svg class="abs hero-art" viewBox="0 0 500 425">
    <path d="M280 55 C360 40 420 90 430 160 C450 260 400 360 300 400 C220 430 150 400 120 330 C80 320 30 300 20 230 C5 150 60 70 140 60 C190 52 230 62 280 55Z" fill="#D8293B"/>
    <path d="M300 80 C400 70 500 140 495 230 C490 330 400 360 330 350 C240 340 180 300 170 230 C160 150 220 88 300 80Z" fill="#FF2B3F"/>
    <circle cx="307" cy="28" r="22" fill="#FF2B3F"/>
    <circle cx="90" cy="307" r="30" fill="#FF2B3F"/>
    <rect x="130" y="10" width="200" height="400" rx="70" fill="#d9d4d4" opacity=".85" role="img" aria-label="Mascot character in a polo shirt pointing to the left"/>
  </svg>
</section>

<section>
  <div class="abs band about-band"></div>
  <svg class="abs about-blob" width="440" height="475" viewBox="0 0 440 475">
    <path d="M80 40 C160 -10 260 0 300 60 C340 120 330 190 370 250 C420 320 440 400 370 450 C300 490 230 460 170 420 C120 390 60 410 20 370 C-10 330 20 270 10 200 C0 130 20 80 80 40Z" fill="#fff"/>
    <path d="M100 380 L168 370 L130 440Z" fill="#FF2B3F"/>
  </svg>
  <div class="abs about-photo" role="img" aria-label="Photo of a man working at a desktop computer in an office"></div>
  <p class="abs eyebrow on-red about-eyebrow">About Us</p>
  <h2 class="abs section-title on-red about-title">Empowering Your Career Journey</h2>
  <p class="abs on-red about-text">At Kestrel Talent, we are dedicated to helping individuals discover their true potential and navigate their career paths with confidence. Our team of experts is committed to providing personalized guidance and support every step of the way</p>
  <a class="abs btn btn-ghost btn-team" href="#">Meet Our Team</a>
</section>

<section>
  <p class="abs eyebrow center why-eyebrow">Why Choose Us</p>
  <h2 class="abs section-title center why-title">What are you looking for?</h2>
  <p class="abs why-lead">At Kestrel Talent, we're seeking skilled professionals across a wide range of disciplines. Our team is highly disciplined and passionate about driving productivity and technology.</p>
  <div class="abs stat" style="left:128px"><p class="stat-label">Talent Pool</p><p class="stat-value">100,000+</p><p class="stat-note">Our talent pool sourced from partnerships,<br>communities, and universities.</p></div>
  <div class="abs stat-rule" style="left:437px"></div>
  <div class="abs stat" style="left:455px"><p class="stat-label">Placed Talent</p><p class="stat-value">7,000+</p><p class="stat-note">Talent successfully placed and working with our<br>clients.</p></div>
  <div class="abs stat-rule" style="left:762px"></div>
  <div class="abs stat" style="left:781px"><p class="stat-label">Satisfied Clients</p><p class="stat-value">150+</p><p class="stat-note">Over the years, we have earned the trust of<br>numerous companies.</p></div>
</section>

<section>
  <div class="abs band proc-band"></div>
  <p class="abs eyebrow center on-red proc-eyebrow">For Business</p>
  <h2 class="abs section-title center on-red proc-title">What's Our Procedure?</h2>
  <p class="abs on-red proc-text">We customize our process to align with your business requirements. A concise consultation with our experts helps us grasp your business needs and talent specifications. We guarantee that the talents we provide meet your precise criteria.</p>
  <p class="abs on-red proc-duration-label">Estimated Consultation Duration:</p>
  <p class="abs on-red proc-duration">30 Minutes</p>
  <div class="abs proc-art" role="img" aria-label="Mascot character leaning and pointing toward the list"></div>
  <ul class="abs on-red proc-steps">
    <li>Consult Your Business Needs</li>
    <li>Talent Assessment</li>
    <li>Select Your Talent</li>
    <li>Paperwork</li>
    <li>Ready-to-Work Talent</li>
    <li>Support</li>
  </ul>
  <a class="abs btn btn-light btn-consult" href="#">
    <svg width="12" height="12" viewBox="0 0 24 24" style="margin-right:6px"><path d="M6.6 10.8c1.4 2.8 3.8 5.1 6.6 6.6l2.2-2.2c.3-.3.7-.4 1-.2 1.1.4 2.300.6 3.6.6.6 0 1 .4 1 1V20c0 .6-.4 1-1 1C10.6 21 3 13.4 3 4c0-.6.4-1 1-1h3.5c.6 0 1 .4 1 1 0 1.3.2 2.5.6 3.6.1.3 0 .7-.2 1z" fill="#C41E2F"/></svg>Consultion now!</a>
</section>

<section>
  <p class="abs eyebrow center ins-eyebrow">Insight</p>
  <h2 class="abs section-title center ins-title">Current Recruitment Trends and Insights</h2>
  <article class="abs card" style="left:120px">
    <div class="card-img" role="img" aria-label="Photo of hands planning at a desk beside a laptop" style="background:linear-gradient(135deg,#6e7778,#a9aea9 50%,#4b5152)"></div>
    <h3 class="card-title">Strategic Talent Acquisition</h3>
    <p class="card-text">Sagittis ipsum varius sed at. Facilisi dui tincidunt aliquam nibh mattis morbi nullam duis aliquam.</p>
    <a class="card-link" href="#">LEARN MORE</a>
  </article>
  <article class="abs card" style="left:447px">
    <div class="card-img" role="img" aria-label="Photo of a person holding a business newspaper" style="background:linear-gradient(135deg,#b7b4ad,#8a8780 50%,#2e2e33)"></div>
    <h3 class="card-title">Salary Insights for 2024</h3>
    <p class="card-text">Fermentum ipsum maecenas ut scelerisque proin tincidunt arcu vulputate. Facilisis mi commodo eu.</p>
    <a class="card-link" href="#">LEARN MORE</a>
  </article>
  <article class="abs card" style="left:773px">
    <div class="card-img" role="img" aria-label="Photo of a laptop, notebook and mug on a wooden desk" style="background:linear-gradient(135deg,#d8d6d0,#b9ab97 55%,#8c7158)"></div>
    <h3 class="card-title">Resilient Workforce for the Future</h3>
    <p class="card-text">Sodales nec viverra fringilla quisque eget lorem ipsum quis id. Adipiscing aliquam etiam varius lorem.</p>
    <a class="card-link" href="#">LEARN MORE</a>
  </article>
  <a class="abs btn btn-outline btn-more" href="#">More Insight</a>
</section>

<section>
  <div class="abs band cta-band" role="img" aria-label="Faint red-tinted photo of an office desk"></div>
  <h2 class="abs section-title on-red cta-title">Need Business Consultation?</h2>
  <p class="abs on-red cta-text">Our business analysts are always ready to listen to your business needs, for <strong>FREE!</strong></p>
  <a class="abs btn btn-light btn-contact" href="#">
    <svg width="13" height="13" viewBox="0 0 24 24" style="margin-right:6px"><path d="M6.6 10.8c1.4 2.8 3.8 5.1 6.6 6.6l2.2-2.2c.3-.3.7-.4 1-.2 1.1.4 2.3.6 3.6.6.6 0 1 .4 1 1V20c0 .6-.4 1-1 1C10.6 21 3 13.4 3 4c0-.6.4-1 1-1h3.5c.6 0 1 .4 1 1 0 1.3.2 2.5.6 3.6.1.3 0 .7-.2 1z" fill="#C41E2F"/></svg>Contact us now!</a>
</section>

<footer>
  <a class="abs brand footer-brand" href="#"><span class="brand-mark"></span>Kestrel Talent</a>
  <div class="abs footer-contact"><p><strong>Contact Us</strong></p><p><strong>Mail:</strong> info@kestreltalent.com</p></div>
  <div class="abs footer-col" style="left:447px"><h4>Job Seekers</h4><p>Find a job</p><p>Industry Info</p><p>Job opportunities</p></div>
  <div class="abs footer-col" style="left:692px"><h4>Business</h4><p>Employers</p><p>Consultations</p><p>Specialties</p></div>
  <div class="abs footer-col" style="left:937px"><h4>Support</h4><p>About Us</p><p>Contact Support</p><p>Our Relations</p></div>
  <div class="abs footer-rule"></div>
  <p class="abs copyright">© 2024 Kestrel Talent. All rights reserved</p>
  <div class="abs social" aria-label="Social links"><span></span><span></span><span></span></div>
</footer>

</body>
</html>
```